Dietitian needs awesome business card

I need a contemporary design that's eye catching but professional.
My card is to given to doctors, specialists and patients alike.
I manage patients with chronic diseases
I have uploaded my logo and current business card, I would also like the other Certified Clinical Nutritionist logo incorporated into the design

Target Market(s)

Doctors, specialists and patients

Industry/Entity Type

Healthcare

Contact Information for Business Card

www.brightfieldnutrition.com.au
Ph: 0427 561 903
Fax: 6457 2183
email: marcus.k.diet@fernmail.com
Space on the back of the card with: Appointment date, Appointment time and appointment location

Font styles to use
Serif

Colors
fbee3e
876aae
ffc214

Requirements
Must have
• My Logo
• Certified Clinical Nutritionist Logo
• My 4 locations - Pinebrook Medical Centre, North Corrin Health, Hollis Medical, Ashcombe Doctors Surgery
Nice to have
• I like the colours in my current business card

```html
<!DOCTYPE html>
<html lang="en">
<head>
<meta charset="utf-8">
<title>Brightfield Nutrition &amp; Dietetics – Business Card</title>
<link rel="stylesheet" href="https://fonts.googleapis.com/css2?family=Source+Sans+3:ital,wght@0,400;0,600;1,600&display=swap">
<style>
  :root {
    --backdrop-top: #2a2a2a;
    --backdrop-bottom: #050505;
    --card: #ffffff;
    --brand-blue: #1b4fa3;
    --navy: #1e2a7a;
    --text-dark: #3a3a3a;
    --rule: #8a86c8;
    --leaf-green: #7cc242;
    --badge-orange: #f26f21;
  }
  * { margin: 0; padding: 0; box-sizing: border-box; }
  html, body { width: 1200px; height: 900px; overflow: hidden; }
  body {
    background: linear-gradient(180deg, var(--backdrop-top) 0%, #151515 55%, var(--backdrop-bottom) 100%);
    font-family: "Source Sans 3", Arial, sans-serif;
    position: relative;
  }
  .card {
    position: absolute;
    top: 306px;
    background: var(--card);
    border-radius: 12px;
    box-shadow: 0 2px 8px rgba(0,0,0,.45);
  }
  .card--front { left: 149px; width: 439px; height: 271px; }
  .card--back  { left: 608px; width: 441px; height: 272px; }

  /* front */
  .front-brand {
    position: absolute; left: 42px; top: 48px; width: 130px;
    display: flex; flex-direction: column; align-items: center; gap: 10px;
  }
  .front-brand__dot {
    width: 64px; height: 64px; border-radius: 50%;
    background: var(--leaf-green);
  }
  .front-brand__name {
    color: var(--brand-blue); font-weight: 600; font-size: 15px;
    text-align: center; line-height: 1.15;
  }
  .holder-name {
    position: absolute; left: 202px; top: 56px;
    color: var(--brand-blue); font-weight: 600; font-size: 16px;
  }
  .contact-list {
    position: absolute; left: 202px; top: 107px; list-style: none;
    color: var(--text-dark); font-size: 12.5px; line-height: 15.7px;
  }
  .contact-list li { display: flex; align-items: center; gap: 6px; }
  .contact-list svg { width: 10px; height: 10px; fill: var(--brand-blue); flex: none; }
  .credential-badge { position: absolute; left: 349px; top: 186px; }
  .credential-line {
    position: absolute; left: 44px; top: 237px;
    color: var(--brand-blue); font-size: 12.5px; letter-spacing: .01em;
    text-transform: uppercase;
  }

  /* back */
  .back-brand {
    position: absolute; left: 96px; top: 34px;
    display: flex; align-items: center; gap: 12px;
  }
  .back-brand__dot {
    width: 62px; height: 62px; border-radius: 50%; background: var(--leaf-green);
  }
  .back-brand__name {
    color: var(--navy); font-weight: 600; font-size: 22px; line-height: 1.1;
  }
  .appointment-title {
    position: absolute; left: 0; right: 0; top: 133px; text-align: center;
    color: var(--brand-blue); font-weight: 600; font-size: 15px;
  }
  .appointment-fields {
    position: absolute; left: 83px; top: 170px; color: var(--brand-blue); font-size: 13px;
  }
  .field-row { display: flex; align-items: flex-end; height: 19px; }
  .field-label { margin-right: 10px; }
  .field-line { border-bottom: 1px solid var(--rule); height: 12px; }
  .notice {
    position: absolute; left: 0; right: 0; top: 222px; text-align: center;
    color: var(--navy); font-style: italic; font-weight: 600; font-size: 12.5px;
  }
</style>
</head>
<body>

<section class="card card--front">
  <div class="front-brand">
    <span class="front-brand__dot"></span>
    <span class="front-brand__name">Brightfield Nutrition</span>
  </div>

  <h1 class="holder-name">Marcus Kellaway</h1>

  <ul class="contact-list">
    <li>
      <svg viewBox="0 0 10 10"><path d="M2 0.5l1.6 0 .6 2.3-1 .8c.6 1.3 1.6 2.3 2.9 2.9l.8-1 2.3.6 0 1.6c0 .8-.6 1.3-1.3 1.3C4 9 1 6 .7 1.8.7 1.1 1.2.5 2 .5z"/></svg>
      0427 561 903
    </li>
    <li>
      <svg viewBox="0 0 10 10"><path d="M2.5 0.5h4v2.5h-4z M0.5 3.5h9v5h-9z" fill-rule="evenodd"/><rect x="2.5" y="6" width="5" height="1" fill="#fff"/></svg>
      6457 2183
    </li>
    <li>
      <svg viewBox="0 0 10 10"><path d="M0.5 2h9v6.5h-9z"/><path d="M0.8 2.3L5 5.6 9.2 2.3" stroke="#fff" stroke-width=".9" fill="none"/></svg>
      marcus.k.diet@fernmail.com
    </li>
    <li>
      <svg viewBox="0 0 10 10"><circle cx="5" cy="5" r="4.5"/><path d="M5 .5v9M.5 5h9M2.5 1.5c1.5 2 1.5 5 0 7M7.5 1.5c-1.5 2-1.5 5 0 7" stroke="#fff" stroke-width=".6" fill="none"/></svg>
      www.brightfieldnutrition.com.au
    </li>
  </ul>

  <svg class="credential-badge" width="46" height="48" viewBox="0 0 46 48" role="img" aria-label="Credential badge">
    <rect x="2" y="2" width="42" height="44" fill="var(--badge-orange)"/>
  </svg>

  <p class="credential-line">Certified Clinical Nutritionist, Nutritionist and Chef</p>
</section>

<section class="card card--back">
  <div class="back-brand">
    <span class="back-brand__dot"></span>
    <span class="back-brand__name">Brightfield<br>Nutrition &amp; Dietetics</span>
  </div>

  <h2 class="appointment-title">Your Next Appointment is</h2>

  <div class="appointment-fields">
    <div class="field-row">
      <span class="field-label">Date:</span>
      <span class="field-line" style="width:86px"></span>
      <span class="field-label" style="margin-left:10px">Time:</span>
      <span class="field-line" style="width:86px"></span>
    </div>
    <div class="field-row">
      <span class="field-label" style="margin-right:4px">Location:</span>
      <span class="field-line" style="width:209px"></span>
    </div>
  </div>

  <p class="notice">If unable to keep appointment, kindly give 24hrs notice.</p>
</section>

</body>
</html>
```